Journal Cover Design Project

The Worldwide Review of Rising Trade Systems is a professional journal which aims to provide an international platform for publication of original research on the emerging economies.
The journal is published three times a year and available by subscription. Currently, the cover design is the same for each issue. We are looking to redesign the cover (and interior) of our journal and would like a design that would allow us to change the color scheme for each issue or volume while maintaining a consistent design scheme.
Our design preference is simple and modern with good use of color. Many of our past publications have used abstract maps/globes but we are open to new ideas. We would need a creative way to include text on the cover, possibly a way to present the article titles or main topics for each issue. For example, we like the use of color and the general design in this image: http://www.pictavo.example/photos/moonlitpaperkite/5120448391/lightbox/
Below is a link to our most recent issue of the journal. You can see an example of the article titles, structure, etc. The website also shows the current cover of the journal (but we do not want the new design to be based off of the current one):
http://wrt.plovarhouse.example/content/4/2.toc

```html
<!DOCTYPE html>
<html lang="en">
<head>
<meta charset="utf-8">
<title>In the news — Worldwide Review of Rising Trade Systems</title>
<link href="https://fonts.googleapis.com/css2?family=Arimo:wght@400;700&display=swap" rel="stylesheet">
<style>
  :root {
    --backdrop: #ffffff;
    --page: #ffffff;
    --green-deep: #176b35;
    --green-bright: #3db54a;
    --green-panel: #d2e9cf;
    --green-tile: #1f9a45;
    --ink: #1c1c1c;
  }
  * { margin: 0; padding: 0; box-sizing: border-box; }
  html, body {
    width: 1200px; height: 849px; overflow: hidden;
    background: var(--backdrop);
    font-family: "Arimo", Arial, sans-serif;
  }
  .page {
    position: absolute; left: 339px; top: 75px;
    width: 522px; height: 684px;
    background: var(--page);
    border: 1px solid #e6e6e6;
  }
  .section-title {
    position: absolute; left: 41px; top: 18px;
    font-size: 24px; font-weight: 400; color: var(--green-deep);
    letter-spacing: -0.2px;
  }
  .rule {
    position: absolute; left: 27px; top: 54px;
    width: 466px; height: 5px; background: var(--green-deep);
  }
  .headline-band {
    position: absolute; left: 27px; top: 59px;
    width: 466px; height: 46px; background: var(--green-bright);
    padding: 7px 0 0 14px;
  }
  .headline {
    font-size: 11.5px; font-weight: 700; color: #fff; line-height: 14px;
  }
  .article-panel {
    position: absolute; left: 27px; top: 109px;
    width: 466px; height: 460px; background: var(--green-panel);
    display: flex; gap: 17px; padding: 9px 0 0 14px;
  }
  .column { width: 210px; }
  .column p {
    font-size: 8.6px; line-height: 12.1px; color: var(--ink);
    margin-bottom: 12.1px;
  }
  .tile-band {
    position: absolute; left: 27px; top: 569px;
    width: 466px; height: 54px;
    background: linear-gradient(180deg, #2ea64d 0%, var(--green-tile) 55%, #178a3c 100%);
  }
  .footer-name {
    position: absolute; left: 27px; top: 634px;
    font-size: 8px; font-weight: 700; color: var(--green-deep);
  }
  .footer-issue {
    position: absolute; left: 27px; top: 644px;
    font-size: 8px; color: var(--green-deep);
  }
  .page-number {
    position: absolute; right: 28px; top: 632px;
    font-size: 20px; color: var(--green-deep);
  }
</style>
</head>
<body>
  <article class="page">
    <h2 class="section-title">In the news</h2>
    <div class="rule"></div>
    <header class="headline-band">
      <h1 class="headline">New Directions for Water Management<br>in Indian Agriculture</h1>
    </header>
    <section class="article-panel">
      <div class="column">
        <p>Despite several decades of large and expensive government programs to expand traditional surface irrigation systems, groundwater irrigated area has continued to grow inexorably—even in command areas of canals and tanks. Groundwater now irrigates more than double the area irrigated by surface water.</p>
        <p>The alarming drop in groundwater tables in parts of Northwestern and of Peninsular India, and the apparent high public cost of subsidizing the electricity for ground water pumping, has led to calls for limiting groundwater abstraction and further developing surface water systems. This reaction to the ground water challenge misses the point.</p>
        <p>The debate should not be about whether surface water schemes are preferable to groundwater use, or more generally how to build new infrastructure to increase water supply. Instead, the question is how to deliver a reliable service to improve agricultural productivity. Further surface water development (reservoirs, canals) will not reduce demand for ground water unless it can meet the requirement for “just-in-time” water without discriminating against tail-enders and/or small farmers.</p>
        <p>Despite several decades of large and expensive government programs to expand traditional</p>
      </div>
      <div class="column">
        <p>surface irrigation systems, groundwater irrigated area has continued to grow inexorably—even in command areas of canals and tanks. Groundwater now irrigates more than double the area irrigated by surface water. The alarming drop in groundwater tables in parts of Northwestern and of Peninsular India, and the apparent high public cost of subsidizing the electricity for ground water pumping, has led to calls for limiting groundwater abstraction and further developing surface water systems. This reaction to the ground water challenge misses the point.</p>
        <p>The debate should not be about whether surface water schemes are preferable to groundwater use, or more generally how to build new infrastructure to increase water supply. Instead, the question is how to deliver a reliable service to improve agricultural productivity. Further surface water development (reservoirs, canals) will not reduce demand for ground water unless it can meet the requirement for “just-in-time” water without discriminating against tail-enders and/or small farmers.</p>
      </div>
    </section>
    <div class="tile-band" role="img" aria-label="Decorative green tiled pattern band"></div>
    <p class="footer-name">WORLDWIDE REVIEW OF RISING TRADE SYSTEMS</p>
    <p class="footer-issue">Vol 4 Issue 2 • May 2012</p>
    <p class="page-number">01</p>
  </article>
</body>
</html>
```